Redesign of business card for Cedar Ridge Mechanical

We are looking for a new design for our business cards for Cedar Ridge Mechanical. We are a plumbing & HVAC construction company, operating on the West Coast of Canada and USA. Logo attached.
Industry/Entity Type
Construction - Plumbing & HVAC
Contact Information for Business Card
Name, address, phone numbers, email, website address
Look and feel
Each slider illustrates characteristics of the customer's brand and the style your logo design should communicate.

```html
<!DOCTYPE html>
<html lang="en">
<head>
<meta charset="utf-8">
<title>Cedar Ridge Mechanical — Business Card</title>
<link rel="stylesheet" href="https://fonts.googleapis.com/css2?family=Montserrat:wght@400;700&display=swap">
<style>
  :root {
    --bg: #e6e6e6;
    --paper: #ffffff;
    --ink: #000000;
    --swoosh: #8a8a8a;
    --on-ink: #ffffff;
    --shadow: rgba(0,0,0,0.28);
  }
  * { margin: 0; padding: 0; box-sizing: border-box; }
  html, body {
    width: 1200px; height: 896px; overflow: hidden;
    background: var(--bg);
    font-family: "Montserrat", sans-serif;
  }
  .card {
    position: absolute;
    left: 334px;
    width: 528px; height: 301px;
    border-radius: 24px;
    background: var(--paper);
    overflow: hidden;
    box-shadow: 0 14px 26px var(--shadow);
  }
  .card--front { top: 126px; }
  .card--back { top: 475px; }

  .brand {
    display: flex; align-items: center; gap: 12px;
    color: var(--ink); font-weight: 700; text-transform: uppercase;
  }
  .brand__mark { background: var(--ink); flex: none; }

  .card--front .brand {
    position: absolute; inset: 0; justify-content: center;
    font-size: 28px; letter-spacing: 1px; line-height: 1.15;
  }
  .card--front .brand__mark { width: 38px; height: 38px; }

  .card--back .brand {
    position: absolute; left: 20px; top: 44px;
    font-size: 19px; letter-spacing: 0.5px; line-height: 1.2;
  }
  .card--back .brand__mark { width: 26px; height: 26px; }

  .back__panel { position: absolute; inset: 0; width: 528px; height: 301px; }

  .contact {
    position: absolute; right: 21px; top: 112px;
    color: var(--on-ink); text-align: right;
  }
  .contact__name { font-size: 19px; font-weight: 700; letter-spacing: 0.6px; line-height: 26px; margin-right: 1px; }
  .contact__role { font-size: 13.5px; line-height: 20px; margin-right: 1px; }
  .contact__list { list-style: none; margin-top: 12px; font-size: 13.5px; }
  .contact__list li { line-height: 21px; display: flex; justify-content: flex-end; align-items: center; gap: 5px; }
  .contact__list svg { width: 12px; height: 12px; fill: var(--on-ink); }
  .contact__address { margin-top: 12px; font-size: 13.5px; line-height: 21px; font-style: normal; }
</style>
</head>
<body>
  <section class="card card--front">
    <div class="brand">
      <span class="brand__mark"></span>
      <span class="brand__name">Cedar Ridge<br>Mechanical</span>
    </div>
  </section>

  <section class="card card--back">
    <svg class="back__panel" viewBox="0 0 528 301" aria-hidden="true">
      <path fill="var(--swoosh)" d="M344,8 C372,50 340,100 290,148 C232,204 198,250 196,301 L206,301 C210,255 246,214 296,160 C350,104 372,52 344,8Z"/>
      <path fill="var(--ink)" d="M352,0 C378,42 352,98 300,150 C246,204 206,252 198,301 L528,301 L528,0Z"/>
    </svg>
    <div class="brand">
      <span class="brand__mark"></span>
      <span class="brand__name">Cedar Ridge<br>Mechanical</span>
    </div>
    <div class="contact">
      <p class="contact__name">DANIEL HAYES</p>
      <p class="contact__role">Managing Director</p>
      <ul class="contact__list">
        <li>123 456 789
          <svg viewBox="0 0 24 24"><path d="M6.6 10.8a15.1 15.1 0 0 0 6.6 6.6l2.2-2.2a1 1 0 0 1 1-.25 11.4 11.4 0 0 0 3.6.57 1 1 0 0 1 1 1V20a1 1 0 0 1-1 1A17 17 0 0 1 3 4a1 1 0 0 1 1-1h3.5a1 1 0 0 1 1 1c0 1.25.2 2.45.57 3.57a1 1 0 0 1-.25 1z"/></svg>
        </li>
        <li>info@yourgmail.com
          <svg viewBox="0 0 24 24"><path d="M2 6h20v2l-10 6L2 8z M2 10l10 6 10-6v8H2z"/></svg>
        </li>
        <li>www.yourwebsite.com
          <svg viewBox="0 0 24 24"><path d="M12 2a10 10 0 1 0 0 20 10 10 0 0 0 0-20zm0 2c1.2 1.4 2 3.5 2.3 6H9.7C10 7.5 10.8 5.4 12 4zM4.1 13h3.6c.1 2 .6 3.8 1.4 5.3A8 8 0 0 1 4.1 13zm0-2a8 8 0 0 1 5-5.3C8.3 7.2 7.8 9 7.7 11zm5.6 2h4.6c-.3 2.5-1.1 4.6-2.3 6-1.2-1.4-2-3.5-2.3-6zm6.6 0h3.6a8 8 0 0 1-5 5.3c.8-1.5 1.3-3.3 1.4-5.3zm0-2c-.1-2-.6-3.8-1.4-5.3a8 8 0 0 1 5 5.3z"/></svg>
        </li>
      </ul>
      <address class="contact__address">Your address, City<br>State, Zip 1234</address>
    </div>
  </section>
</body>
</html>
```